Biz Card

MARKETING today is the most rapidly changing business discipline. Media options to reach customers, actual customer preferences and consumer buying decisions change by the minute . . . no, by the second. The behavioral data generated by all aspects of the business and the new technologies that put the data to work together produce the potential to generate business intelligence and guide smart resource allocation to influence purchase and retention. However, to realize this potential, marketing professionals at all levels and in all organizations must continuously improve their skills not just from on-the-job training but by learning from masters in the field. The Bright Horizon Guild is the training center that serves this professional development need.model logos:msi.orgama.orgcontentmarketinginstitute.comBook covers on MarketingMetrics, Marketing Anaytics
Industry/Entity Type
Business
Contact Information for Business Card
Roy A. YoungCEOMarketing Science Academyphone: 310-601-4755email: roy@marketingscience.comAddress:437 South Rexford DriveBeverly Hills, CA 89377
Look and feel
Each slider illustrates characteristics of the customer's brand and the style your logo design should communicate.

```html
<!DOCTYPE html>
<html lang="en">
<head>
<meta charset="utf-8">
<title>Bright Horizon Guild – Business Card</title>
<link rel="stylesheet" href="https://fonts.googleapis.com/css2?family=Archivo:wght@700&family=Roboto:wght@400;700&family=Roboto+Condensed:wght@700&display=swap">
<style>
  :root {
    --backdrop: #aeacac;
    --brand-red: #8b2926;
    --ink-grey: #4a4a4c;
    --swoosh-grey: #4d4d4f;
    --paper: #fbfbfb;
    --white: #ffffff;
  }
  * { margin: 0; padding: 0; box-sizing: border-box; }
  html, body {
    width: 1200px; height: 1200px; overflow: hidden;
    background: var(--backdrop);
  }
  .canvas { position: relative; width: 1200px; height: 1200px; }

  .card { position: absolute; overflow: hidden; }

  /* Front */
  .card-front {
    left: 238px; top: 118px; width: 713px; height: 419px;
    background: var(--brand-red);
    display: flex; align-items: center; justify-content: center; gap: 16px;
  }
  .brand-name {
    font-family: "Archivo", sans-serif; font-weight: 700;
    letter-spacing: 0.5px; line-height: 1;
  }
  .card-front .brand-name { color: var(--white); font-size: 40px; }
  .brand-dot { border-radius: 50%; flex: none; }
  .card-front .brand-dot { width: 22px; height: 22px; background: var(--white); }

  /* Back */
  .card-back {
    left: 230px; top: 645px; width: 712px; height: 416px;
    background: var(--paper);
  }
  .back-brand {
    position: absolute; left: 43px; top: 86px;
    display: flex; align-items: center; gap: 14px;
  }
  .card-back .brand-name { color: var(--brand-red); font-size: 38px; }
  .card-back .brand-dot { width: 20px; height: 20px; background: var(--brand-red); }

  .address {
    position: absolute; left: 43px; top: 206px;
    font-family: "Roboto", sans-serif; font-size: 17px; color: var(--ink-grey);
  }
  .contact-list {
    position: absolute; left: 43px; top: 244px; list-style: none;
    font-family: "Roboto", sans-serif; font-size: 17px; color: var(--ink-grey);
  }
  .contact-list li { display: flex; align-items: center; gap: 20px; height: 24px; }
  .contact-list svg { width: 15px; height: 15px; fill: var(--brand-red); flex: none; }

  .wave { position: absolute; left: 0; top: 0; width: 712px; height: 416px; }

  .person {
    position: absolute; right: 42px; top: 320px; text-align: right;
    color: var(--white);
  }
  .person-name { font-family: "Roboto Condensed", sans-serif; font-weight: 700; font-size: 27px; }
  .person-title { font-family: "Roboto", sans-serif; font-size: 15px; margin-top: 8px; }
</style>
</head>
<body>
<main class="canvas">

  <section class="card card-front" aria-label="Card front">
    <span class="brand-name">BRIGHT HORIZON GUILD</span>
    <span class="brand-dot"></span>
  </section>

  <section class="card card-back" aria-label="Card back">
    <svg class="wave" viewBox="0 0 712 416" aria-hidden="true">
      <path fill="var(--brand-red)" d="M0,385 C200,402 420,362 560,292 C620,262 670,242 712,240 L712,416 L0,416 Z"/>
      <path fill="var(--swoosh-grey)" d="M0,345 C180,382 380,372 520,290 C600,244 660,222 712,216 L712,230 C650,238 590,262 522,304 C380,388 160,388 0,362 Z"/>
    </svg>

    <div class="back-brand">
      <span class="brand-name">BRIGHT HORIZON GUILD</span>
      <span class="brand-dot"></span>
    </div>

    <p class="address">912 North Calloway Lane Beverly Hills, CA 89377</p>

    <ul class="contact-list">
      <li>
        <svg viewBox="0 0 16 16" aria-hidden="true"><path d="M1 5c0-2 2-3 7-3s7 1 7 3v1h-4V5H5v1H1zM3 8l2-2h6l2 2v6H3zm5 1.5a2 2 0 1 0 0 4 2 2 0 0 0 0-4z"/></svg>
        <span>310-555-0182</span>
      </li>
      <li>
        <svg viewBox="0 0 16 16" aria-hidden="true"><path d="M1 3h14v10H1zm1.5 1.5L8 9l5.5-4.5v-.2h-11z" fill-rule="evenodd"/></svg>
        <span>neil@brighthorizonguild.com</span>
      </li>
      <li>
        <svg viewBox="0 0 16 16" aria-hidden="true"><circle cx="8" cy="8" r="7"/><path d="M1 8h14M8 1c-3 3-3 11 0 14M8 1c3 3 3 11 0 14" stroke="#fff" stroke-width="1" fill="none"/></svg>
        <span>www.brighthorizonguild.com</span>
      </li>
    </ul>

    <div class="person">
      <p class="person-name">Neil P. Barton</p>
      <p class="person-title">CEO</p>
    </div>
  </section>

</main>
</body>
</html>
```